Sustainably Transforming Education

Company is education services based. early learning through adult and corporate. Focus is national government policy and program design and delivery alongside a research based and academically grounded set of approaches to planning, evaluation, and change management.I am looking for an innovative design position that aligns with the global agendas for innovation, creativity and collaboration at international and national policy levels (berulo is a name that reflects these qualities - colours need to reflect amythyst in some way). I also need a design that translates from a business card as 1 medium of interaction to a template that can work in word/powerpoint etc to support both stationery as well as a digital strategy across multiple channels (fb/twit/etc)There is no slogan/tag line for the company and their is no logo. I was looking to just leverage the name - have currently played around with various fonts (ending up with cuisine - all lowercase).

Industry/Entity Type

Adult

Contact Information for Business Card

name: berulo (all lowercase)Chairman: Andrew CrowMobile: +61 418 902 131Web: www.berulo.comemail: martin.pelly@berulo-example.com

Font styles to use
Script
Other font styles liked:
• cuisine

Colors
e34298
e667a6
33a6d7
aaaaaa

Requirements
Nice to have
• https://files.example-share.net/sh/qx7kw2hd91lzmnp/AAFr3tYbQeLp8VwZnKcDs2Hu?dl=0
• Link to the printwell templates used to begin this process....the one with the lines was about people intersecting (collaborating).....the organic shapes one more of a fluid feel of people coming together - the overall shape being largely spherical could represent a "global" feel.....anyway that is how I was thinking about these

```html
<!DOCTYPE html>
<html lang="en">
<head>
<meta charset="utf-8">
<title>berulo business card</title>
<link rel="stylesheet" href="https://fonts.googleapis.com/css2?family=Courgette&family=Merienda:wght@700&display=swap">
<style>
  :root {
    --card-blue: #33a6d7;
    --amethyst: #e34298;
    --amethyst-soft: #e667a6;
    --ink-white: #ffffff;
    --ink-dark: #222222;
    --ink-icon: #4a1a36;
  }
  * { margin: 0; padding: 0; box-sizing: border-box; }
  html, body { width: 1200px; height: 740px; overflow: hidden; background: var(--card-blue); }
  .card {
    position: relative;
    width: 1200px;
    height: 740px;
    background: var(--card-blue);
    overflow: hidden;
  }
  .world-map {
    position: absolute;
    left: 0;
    top: 204px;
    width: 474px;
    height: 384px;
  }
  .brand-name {
    position: absolute;
    left: 24px;
    top: 334px;
    font-family: "Courgette", cursive;
    font-size: 84px;
    line-height: 1;
    color: var(--ink-white);
  }
  .person-name {
    position: absolute;
    right: 78px;
    top: 74px;
    font-family: "Courgette", cursive;
    font-size: 92px;
    line-height: 1.1;
    color: var(--ink-white);
    white-space: nowrap;
  }
  .person-title {
    position: absolute;
    right: 82px;
    top: 196px;
    font-family: "Courgette", cursive;
    font-size: 46px;
    line-height: 1.1;
    color: var(--ink-dark);
  }
  .contact-list {
    position: absolute;
    left: 684px;
    top: 492px;
    list-style: none;
  }
  .contact-item {
    display: flex;
    align-items: center;
    height: 46px;
  }
  .contact-icon {
    width: 30px;
    height: 30px;
    margin-right: 30px;
    flex: none;
  }
  .contact-text {
    font-family: "Merienda", cursive;
    font-weight: 700;
    font-size: 21px;
    color: var(--ink-white);
    white-space: nowrap;
  }
</style>
</head>
<body>
<div class="card">
  <svg class="world-map" viewBox="0 0 474 384" role="img" aria-label="Faint world map silhouette showing the continents">
    <defs>
      <linearGradient id="mapFade" x1="0" y1="0" x2="1" y2="1">
        <stop offset="0" stop-color="#e667a6" stop-opacity="0.7"/>
        <stop offset="1" stop-color="#e34298" stop-opacity="0.45"/>
      </linearGradient>
    </defs>
    <rect x="0" y="0" width="474" height="384" rx="60" fill="url(#mapFade)"/>
  </svg>

  <div class="brand-name">berulo</div>

  <div class="person-name">Martin Pelly</div>
  <div class="person-title">Chairman</div>

  <ul class="contact-list">
    <li class="contact-item">
      <svg class="contact-icon" viewBox="0 0 24 24" aria-hidden="true">
        <path d="M3 8c0-2 2-3 9-3s9 1 9 3v1.5h-4V8H7v1.5H3z" fill="var(--amethyst)"/>
        <path d="M6 11h12l2 8H4z" fill="var(--amethyst)"/>
        <rect x="9" y="12.5" width="6" height="4" fill="var(--card-blue)"/>
      </svg>
      <span class="contact-text">+61 427 315 086</span>
    </li>
    <li class="contact-item">
      <svg class="contact-icon" viewBox="0 0 24 24" aria-hidden="true">
        <rect x="2" y="5" width="20" height="14" fill="var(--amethyst)"/>
        <path d="M2.5 5.5 12 13l9.5-7.5" fill="none" stroke="var(--card-blue)" stroke-width="1.4"/>
        <path d="M2.5 18.5 9.5 11.5M21.5 18.5 14.5 11.5" fill="none" stroke="var(--card-blue)" stroke-width="1.2"/>
      </svg>
      <span class="contact-text">martin.pelly@berulo-example.com</span>
    </li>
    <li class="contact-item">
      <svg class="contact-icon" viewBox="0 0 24 24" aria-hidden="true">
        <g fill="none" stroke="var(--amethyst)" stroke-width="1.8">
          <circle cx="12" cy="12" r="9.5"/>
          <ellipse cx="12" cy="12" rx="4" ry="9.5"/>
          <path d="M2.5 12h19M4 7h16M4 17h16"/>
        </g>
      </svg>
      <span class="contact-text">www.berulo-example.com</span>
    </li>
  </ul>
</div>
</body>
</html>
```